Whitcombe Business Card Design

The name of the business is Dario Whitcombe, CPA LLC
The service that we offer is Accounting, Tax & Consulting Services. I need it to have the following items:
Dario Whitcombe, Principal
Phone Number
Email Address
Physical Address

I have attached the company logo, one in black and one in white. Please provide a design in black background and the other in white background. Please include "Accounting, Tax & Consulting Services". I want the business card to be clean and very professional.

```html
<!DOCTYPE html>
<html lang="en">
<head>
<meta charset="utf-8">
<title>Dario Whitcombe, CPA LLC – Business Cards</title>
<link href="https://fonts.googleapis.com/css2?family=Montserrat:wght@500;600;700&family=Roboto:wght@300;400&display=swap" rel="stylesheet">
<style>
  :root {
    --backdrop: #2b2b2c;
    --card-dark: #232325;
    --card-dark-edge: #2e2e31;
    --card-light: #efefef;
    --brand-red: #8c1419;
    --edge-grey: #9a9a9c;
    --ink: #2a2a2c;
    --ink-soft: #555558;
    --muted: #8a8a8c;
    --white: #ffffff;
  }
  * { margin: 0; padding: 0; box-sizing: border-box; }
  html, body { width: 1200px; height: 1138px; overflow: hidden; }
  body { background: var(--backdrop); position: relative; font-family: "Roboto", sans-serif; }

  .card { position: absolute; border-radius: 14px; overflow: hidden; }

  /* Front card (dark) */
  .card-front {
    left: 272px; top: 184px; width: 622px; height: 376px;
    background: linear-gradient(160deg, var(--card-dark) 0%, var(--card-dark-edge) 100%);
  }
  .front-mark {
    position: absolute; left: 281px; top: 112px; width: 60px; height: 60px;
    border: 6px solid var(--white);
  }
  .front-name {
    position: absolute; left: 0; right: 0; top: 214px; text-align: center;
    font-family: "Montserrat", sans-serif; font-weight: 600; font-size: 24px;
    letter-spacing: 0.5px; color: var(--white); text-transform: uppercase; white-space: nowrap;
  }
  .front-tag {
    position: absolute; left: 0; right: 0; top: 249px; text-align: center;
    font-family: "Montserrat", sans-serif; font-weight: 600; font-size: 13.5px;
    letter-spacing: 1.6px; color: var(--muted); text-transform: uppercase; white-space: nowrap;
  }

  /* Back card (light) */
  .card-back {
    left: 274px; top: 606px; width: 619px; height: 375px;
    background: linear-gradient(180deg, #f6f6f6 0%, var(--card-light) 100%);
  }
  .back-shape { position: absolute; left: 0; top: 0; }
  .back-panel-name {
    position: absolute; left: 24px; top: 168px; width: 200px;
    font-family: "Montserrat", sans-serif; font-weight: 600; font-size: 22px;
    line-height: 1.25; color: var(--white); text-transform: uppercase; letter-spacing: 0.5px;
  }
  .back-info { position: absolute; right: 27px; text-align: right; white-space: nowrap; }
  .wordmark {
    top: 40px; font-family: "Montserrat", sans-serif; font-weight: 600; font-size: 19.5px;
    color: var(--ink); text-transform: uppercase; letter-spacing: 0.4px;
  }
  .tagline {
    top: 68px; font-family: "Montserrat", sans-serif; font-weight: 600; font-size: 11.5px;
    color: var(--muted); text-transform: uppercase; letter-spacing: 1.1px;
  }
  .person-name {
    top: 153px; font-family: "Montserrat", sans-serif; font-weight: 700; font-size: 18px;
    color: var(--brand-red); text-transform: uppercase; letter-spacing: 0.6px;
  }
  .person-role { top: 178px; font-weight: 300; font-size: 15px; color: var(--ink-soft); }
  .address { top: 224px; font-weight: 300; font-size: 15px; line-height: 24px; color: var(--ink-soft); }
  .contact-list { top: 279px; list-style: none; }
  .contact-list li {
    display: flex; justify-content: flex-end; align-items: center; gap: 12px;
    height: 24px; font-weight: 300; font-size: 15px; color: var(--ink-soft);
  }
  .contact-list svg { width: 14px; height: 14px; fill: var(--brand-red); }
</style>
</head>
<body>

<section class="card card-front" aria-label="Business card front">
  <div class="front-mark"></div>
  <p class="front-name">Dario Whitcombe, CPA LLC</p>
  <p class="front-tag">Accounting, Tax &amp; Consulting Services</p>
</section>

<section class="card card-back" aria-label="Business card back">
  <svg class="back-shape" width="619" height="375" viewBox="0 0 619 375">
    <path d="M0 0 H215 Q300 187 211 375 H0 Z" fill="var(--edge-grey)"/>
    <path d="M0 0 H203 Q288 187 199 375 H0 Z" fill="var(--brand-red)"/>
  </svg>
  <p class="back-panel-name">Dario<br>Whitcombe</p>

  <p class="back-info wordmark">Dario Whitcombe, CPA LLC</p>
  <p class="back-info tagline">Accounting, Tax &amp; Consulting Services</p>
  <p class="back-info person-name">Dario Whitcombe</p>
  <p class="back-info person-role">Principal</p>
  <p class="back-info address">58 Larkfield Road, Suite 4,<br>Brookvale, OR 97301</p>
  <ul class="back-info contact-list">
    <li>555-014-2290
      <svg viewBox="0 0 16 16" aria-hidden="true"><path d="M2 6c0-2 2-3 6-3s6 1 6 3v1h-3V5.5H5V7H2z M4 8h8l1 6H3z"/></svg>
    </li>
    <li>dw@whitcombecpa.com
      <svg viewBox="0 0 16 16" aria-hidden="true"><path d="M1 3h14v10H1z M2.5 4.5 8 9l5.5-4.5" stroke="#efefef" stroke-width="1.2"/></svg>
    </li>
    <li>www.whitcombecpa.com
      <svg viewBox="0 0 16 16" aria-hidden="true"><circle cx="8" cy="8" r="7"/><path d="M1 8h14 M8 1v14 M8 1c-3 3-3 11 0 14 M8 1c3 3 3 11 0 14" stroke="#efefef" stroke-width="0.9" fill="none"/></svg>
    </li>
  </ul>
</section>

</body>
</html>
```